Heron Loan Partners Business Card

We need a business card design for our mortgage servicing company. In addition to servicing the loans of homeowners, we help homeowners with purchasing their homes and any mortgage refinancing. We would like to see designs that use the colors in the logo attached below (gold-ish yellow and navy blue), and any other design you deem fit! The design should communicate a simpler life with smart mortgages provided by Heron.

```html
<!DOCTYPE html>
<html lang="en">
<head>
<meta charset="utf-8">
<title>Heron Loan Partners – Business Card</title>
<link rel="stylesheet" href="https://fonts.googleapis.com/css2?family=Libre+Baskerville:wght@400;700&family=Lato:wght@400;700&display=swap">
<style>
  :root {
    --navy: #28215a;
    --gold: #e0b03c;
    --white: #ffffff;
    --rule: #6f6a96;
    --backdrop: #1d1d1f;
  }
  * { box-sizing: border-box; margin: 0; padding: 0; }
  html, body {
    width: 1200px; height: 1015px; overflow: hidden;
    background: var(--backdrop);
    font-family: "Lato", sans-serif;
  }
  .sheet {
    width: 1200px; height: 1015px;
    display: flex; flex-direction: column; align-items: center; justify-content: center;
    gap: 64px;
  }
  .card {
    position: relative;
    width: 640px; height: 366px;
    overflow: hidden;
    box-shadow: 0 18px 40px rgba(0,0,0,.55);
  }
  .card--front { background: var(--navy); }
  .card--back { background: var(--navy); }

  .wordmark {
    font-family: "Libre Baskerville", serif;
    font-weight: 700;
    color: var(--gold);
    white-space: nowrap;
    display: flex; align-items: center; gap: 12px;
  }
  .wordmark__dot {
    width: 14px; height: 14px; border-radius: 50%;
    background: currentColor;
  }

  .front__logo {
    position: absolute; left: 0; right: 0; top: 118px;
    justify-content: center;
    font-size: 38px;
  }
  .front__web {
    position: absolute; left: 0; right: 0; top: 232px;
    display: flex; align-items: center; justify-content: center; gap: 18px;
    font-size: 15px; letter-spacing: 4px; color: var(--white);
  }
  .front__web .accent { color: var(--gold); }
  .front__rule { width: 110px; height: 1px; background: var(--rule); }

  .back__shape { position: absolute; inset: 0; }
  .back__logo {
    position: absolute; left: 36px; top: 206px;
    font-size: 22px; gap: 10px; color: var(--navy);
  }
  .back__logo .wordmark__dot { width: 12px; height: 12px; }
  .back__info {
    position: absolute; right: 34px; top: 34px;
    text-align: right; color: var(--white);
  }
  .back__name {
    font-family: "Libre Baskerville", serif;
    font-size: 22px; color: var(--gold);
  }
  .back__title { font-size: 15px; margin-top: 2px; }
  .back__rule {
    width: 56px; height: 2px; background: var(--gold);
    margin: 16px 0 16px auto;
  }
  .back__address { font-size: 15px; line-height: 1.3; }
  .back__contacts { list-style: none; font-size: 15px; line-height: 1.45; margin-top: 22px; }
  .back__contacts li { display: flex; align-items: center; justify-content: flex-end; gap: 8px; }
  .icon { width: 14px; height: 14px; flex: none; }
</style>
</head>
<body>
<main class="sheet">

  <section class="card card--front" aria-label="Card front">
    <div class="wordmark front__logo">
      <span class="wordmark__dot"></span>Heron Loan Partners
    </div>
    <div class="front__web">
      <span class="front__rule"></span>
      <span>www.<span class="accent">websitename</span>.com</span>
      <span class="front__rule"></span>
    </div>
  </section>

  <section class="card card--back" aria-label="Card back">
    <svg class="back__shape" viewBox="0 0 640 366" preserveAspectRatio="none" aria-hidden="true">
      <path d="M0,0 L300,0 Q360,84 500,92 Q380,210 360,366 L0,366 Z" fill="var(--gold)"/>
      <path d="M0,0 L286,0 Q346,74 500,92 Q364,200 342,366 L0,366 Z" fill="var(--white)"/>
    </svg>

    <div class="wordmark back__logo">
      <span class="wordmark__dot"></span>Heron Loan Partners
    </div>

    <div class="back__info">
      <p class="back__name">Daniel Hartley</p>
      <p class="back__title">Managing Director</p>
      <div class="back__rule"></div>
      <p class="back__address">421, Address line<br>goes here 45452<br>Country Name</p>
      <ul class="back__contacts">
        <li>044-123 456 789
          <svg class="icon" viewBox="0 0 16 16" aria-hidden="true"><path fill="var(--gold)" d="M3.6 1.5l2.3 2.6-1.2 1.9c.9 2 2.6 3.7 4.6 4.6l1.9-1.2 2.6 2.3-1.3 2.3C7.4 15.3.7 8.6 1.3 2.8z"/></svg>
        </li>
        <li>info@webname.com
          <svg class="icon" viewBox="0 0 16 16" aria-hidden="true"><rect x="1" y="3" width="14" height="10" fill="var(--gold)"/><path d="M1 3l7 6 7-6" fill="none" stroke="var(--navy)" stroke-width="1.3"/></svg>
        </li>
        <li>www.websitename.com
          <svg class="icon" viewBox="0 0 16 16" aria-hidden="true"><g fill="none" stroke="var(--gold)" stroke-width="1.4"><circle cx="8" cy="8" r="6.5"/><ellipse cx="8" cy="8" rx="2.8" ry="6.5"/><path d="M1.5 8h13M2.6 4.5h10.8M2.6 11.5h10.8"/></g></svg>
        </li>
      </ul>
    </div>
  </section>

</main>
</body>
</html>
```